Request for Business Card Design

Hi. My name is Marlene, I am looking for a new business card design for my company, Quarrow Signal Instruments, LLC. I really like the design you did for Tarsel Venture and was hoping you could do something similar using our full logo and our mark. I am also open to any raised texture design using our mark. I have attached our full logo, which would need to be somewhere on the card, as well as the mark in both outline and full form, as well as our brand colors / guide. The card does not have to be white, as long as our logo and mark appear. I actually like darker colored business cards more, but am open to all options. If you are interested in working with me, please let me know. We would also take the business card design into letterhead design if you can do that.

```html
<!DOCTYPE html>
<html lang="en">
<head>
<meta charset="utf-8">
<title>Quarrow Signal Instruments – Business Card</title>
<link rel="stylesheet" href="https://fonts.googleapis.com/css2?family=Open+Sans:wght@400;600;700;800&display=swap">
<style>
  :root {
    --stage: #232323;
    --card-dark: #3d3d3f;
    --brand-blue: #1a9ac6;
    --brand-blue-deep: #1489b3;
    --white: #ffffff;
    --muted: #e9e9ea;
  }
  * { box-sizing: border-box; margin: 0; padding: 0; }
  html, body {
    width: 1200px; height: 780px; overflow: hidden;
    background: var(--stage);
    font-family: "Open Sans", Arial, sans-serif;
  }
  .stage {
    position: relative; width: 1200px; height: 780px;
    display: flex; justify-content: center; align-items: center; gap: 56px;
  }
  .card {
    position: relative; width: 340px; height: 600px;
    box-shadow: 0 18px 40px rgba(0,0,0,.55);
    overflow: hidden;
  }

  /* Front: blue pattern side */
  .card--front { background: var(--brand-blue); }
  .front-pattern {
    position: absolute; inset: 0;
    background: linear-gradient(160deg, #4cb6da 0%, var(--brand-blue) 38%, var(--brand-blue-deep) 100%);
  }
  .front-brand {
    position: absolute; top: 28px; right: 26px;
    display: flex; flex-direction: column; align-items: center; gap: 12px;
  }
  .front-brand__name {
    writing-mode: vertical-rl;
    color: var(--white);
    font-weight: 700; font-size: 15px; letter-spacing: 2px;
    text-transform: uppercase;
  }
  .front-brand__dot {
    width: 22px; height: 22px; border-radius: 50%;
    background: var(--white);
  }

  /* Back: dark info side */
  .card--back { background: var(--card-dark); }
  .back-edge {
    position: absolute; left: 0; top: 0; bottom: 0; width: 5px;
    background: var(--brand-blue);
  }
  .back-brand {
    position: absolute; top: 58px; left: 0; right: 0;
    display: flex; align-items: center; justify-content: center; gap: 12px;
  }
  .back-brand__dot {
    width: 34px; height: 34px; border-radius: 50%;
    background: var(--brand-blue);
  }
  .back-brand__name {
    color: var(--white);
    font-weight: 700; font-size: 16px; line-height: 1.15;
    letter-spacing: 1.2px; text-transform: uppercase;
  }
  .person {
    position: absolute; top: 318px; right: 86px; text-align: right;
  }
  .person__name {
    color: var(--brand-blue);
    font-weight: 800; font-size: 40px; line-height: 1;
    letter-spacing: .5px;
  }
  .person__role {
    color: var(--white); font-weight: 600; font-size: 14px;
    margin-top: 2px; margin-right: 14px;
  }
  .contact {
    position: absolute; top: 412px; left: 34px; right: 20px;
    color: var(--muted); font-size: 13.5px; line-height: 1.4;
  }
  .contact__address { margin-bottom: 14px; }
  .contact__list { list-style: none; padding-left: 8px; }
  .contact__item {
    display: flex; align-items: center; gap: 10px;
    font-size: 13px; line-height: 1.55;
  }
  .contact__icon { width: 13px; height: 13px; flex: none; fill: var(--brand-blue); }
</style>
</head>
<body>
<main class="stage">

  <section class="card card--front" aria-label="Card front">
    <div class="front-pattern" role="img" aria-label="Repeating brand mark pattern in light and deep blue tones"></div>
    <div class="front-brand">
      <span class="front-brand__dot"></span>
      <span class="front-brand__name">Quarrow Signal Instruments</span>
    </div>
  </section>

  <section class="card card--back" aria-label="Card back">
    <span class="back-edge"></span>
    <header class="back-brand">
      <span class="back-brand__dot"></span>
      <span class="back-brand__name">Quarrow<br>Signal Instruments</span>
    </header>

    <div class="person">
      <h1 class="person__name">Marlene</h1>
      <p class="person__role">Director</p>
    </div>

    <div class="contact">
      <p class="contact__address">1180 Fenwick Park Road •<br>Aldermoor, CO 80177</p>
      <ul class="contact__list">
        <li class="contact__item">
          <svg class="contact__icon" viewBox="0 0 24 24" aria-hidden="true"><path d="M6.6 10.8a15 15 0 0 0 6.6 6.6l2.2-2.2a1 1 0 0 1 1-.25 11.4 11.4 0 0 0 3.6.6 1 1 0 0 1 1 1V20a1 1 0 0 1-1 1A17 17 0 0 1 3 4a1 1 0 0 1 1-1h3.5a1 1 0 0 1 1 1c0 1.25.2 2.45.6 3.6a1 1 0 0 1-.25 1z"/></svg>
          +001 555 210 4830
        </li>
        <li class="contact__item">
          <svg class="contact__icon" viewBox="0 0 24 24" aria-hidden="true"><path d="M6 2h9l3 3v5h1a3 3 0 0 1 3 3v7a2 2 0 0 1-2 2H4a2 2 0 0 1-2-2v-7a3 3 0 0 1 3-3h1zm2 2v6h8V6h-2V4zm-3 9v2h3v-2zm7 1v2h2v-2zm4 0v2h2v-2z"/></svg>
          +001 555 210 4831
        </li>
        <li class="contact__item">
          <svg class="contact__icon" viewBox="0 0 24 24" aria-hidden="true"><path d="M12 2a10 10 0 1 0 0 20 10 10 0 0 0 0-20zm-1 17.9A8 8 0 0 1 4.2 10.8L9 15.6v1a2 2 0 0 0 2 2zm6.9-2.5A2 2 0 0 0 16 16h-1v-3a1 1 0 0 0-1-1H8v-2h2a1 1 0 0 0 1-1V7h2a2 2 0 0 0 2-2v-.4a8 8 0 0 1 2.9 12.8z"/></svg>
          www.quarrowsignal.com
        </li>
        <li class="contact__item">
          <svg class="contact__icon" viewBox="0 0 24 24" aria-hidden="true"><path d="M3 5h18a1 1 0 0 1 1 1v12a1 1 0 0 1-1 1H3a1 1 0 0 1-1-1V6a1 1 0 0 1 1-1zm1 2.2V17h16V7.2l-8 5.3z"/></svg>
          info@quarrowsignal.com
        </li>
      </ul>
    </div>
  </section>

</main>
</body>
</html>
```